Residential Remodeling Contractor needs updated business card

I need a new design for my business card.
Name of the company is Ridgefell Construction. I need a card that commands presence, strength, integrity. I have been in business for 28 years. I am a Residential Remodeling Contractor that covers all aspects of a residential remodel and build.

```html
<!DOCTYPE html>
<html lang="en">
<head>
<meta charset="utf-8">
<title>Ridgefell Construction – Business Card</title>
<link rel="stylesheet" href="https://fonts.googleapis.com/css2?family=Open+Sans:wght@400;600;700&display=swap">
<style>
  :root {
    --backdrop: #222222;
    --card-blue: #213d7a;
    --card-edge: #1a3163;
    --ink: #ffffff;
    --ink-soft: rgba(255, 255, 255, 0.85);
    --rule: rgba(255, 255, 255, 0.55);
  }
  * { box-sizing: border-box; margin: 0; padding: 0; }
  html, body {
    width: 1200px;
    height: 780px;
    overflow: hidden;
    background: var(--backdrop);
    font-family: "Open Sans", Arial, sans-serif;
    color: var(--ink);
  }
  .canvas {
    width: 1200px;
    height: 780px;
    display: flex;
    align-items: center;
    justify-content: center;
    gap: 40px;
  }
  .card {
    position: relative;
    width: 520px;
    height: 297px;
    background: var(--card-blue);
    box-shadow: 0 3px 0 var(--card-edge), 0 6px 0 var(--card-edge), 0 18px 40px rgba(0, 0, 0, 0.5);
  }

  /* Company name lockup */
  .wordmark {
    display: flex;
    align-items: center;
    gap: 12px;
    font-weight: 600;
    color: var(--ink);
    letter-spacing: 0.06em;
    text-transform: uppercase;
    line-height: 1.1;
  }
  .wordmark__square {
    flex: none;
    background: var(--ink);
  }

  /* Back: contact side */
  .card--contact .wordmark {
    position: absolute;
    left: 34px;
    top: 64px;
    font-size: 19px;
  }
  .card--contact .wordmark__square { width: 30px; height: 30px; }
  .divider {
    position: absolute;
    left: 262px;
    top: 58px;
    width: 1px;
    height: 170px;
    background: var(--rule);
  }
  .person {
    position: absolute;
    left: 286px;
    top: 66px;
  }
  .person__name {
    font-size: 25px;
    font-weight: 700;
    line-height: 1.1;
  }
  .person__title {
    font-size: 13px;
    color: var(--ink-soft);
    margin-top: 4px;
  }
  .contacts {
    list-style: none;
    margin-top: 16px;
    font-size: 12.5px;
    line-height: 1.75;
  }
  .contacts li { display: flex; align-items: center; gap: 8px; }
  .contacts svg { width: 12px; height: 12px; flex: none; }
  .address {
    position: absolute;
    left: 34px;
    bottom: 26px;
    font-size: 11.5px;
    color: var(--ink-soft);
  }

  /* Front: brand side */
  .card--brand {
    display: flex;
    align-items: center;
    justify-content: center;
  }
  .card--brand .wordmark {
    font-size: 32px;
    gap: 18px;
  }
  .card--brand .wordmark__square { width: 50px; height: 50px; }
</style>
</head>
<body>
<main class="canvas">
  <section class="card card--contact" aria-label="Business card, contact side">
    <div class="wordmark">
      <span class="wordmark__square"></span>
      <span>Ridgefell<br>Construction</span>
    </div>
    <div class="divider"></div>
    <div class="person">
      <p class="person__name">Daniel Hartwell</p>
      <p class="person__title">Managing Director</p>
      <ul class="contacts">
        <li>
          <svg viewBox="0 0 24 24" fill="#fff" aria-hidden="true"><path d="M6.6 10.8a15.1 15.1 0 0 0 6.6 6.6l2.2-2.2a1 1 0 0 1 1-.25 11.4 11.4 0 0 0 3.6.57 1 1 0 0 1 1 1V20a1 1 0 0 1-1 1A17 17 0 0 1 3 4a1 1 0 0 1 1-1h3.5a1 1 0 0 1 1 1c0 1.25.2 2.45.57 3.57a1 1 0 0 1-.25 1z"/></svg>
          (555) 014-2280
        </li>
        <li>
          <svg viewBox="0 0 24 24" fill="#fff" aria-hidden="true"><path d="M2 5h20v14H2z" fill="none" stroke="#fff" stroke-width="2"/><path d="M2 5l10 8 10-8" fill="none" stroke="#fff" stroke-width="2"/></svg>
          info@ridgefellbuild.com
        </li>
        <li>
          <svg viewBox="0 0 24 24" fill="none" stroke="#fff" stroke-width="2" aria-hidden="true"><circle cx="12" cy="12" r="10"/><path d="M2 12h20M12 2c3 3 3 17 0 20M12 2c-3 3-3 17 0 20"/></svg>
          www.ridgefellbuild.com
        </li>
      </ul>
    </div>
    <p class="address">1840 Alder Crest Dr. Suite 310 Millbrook, TX 76540</p>
  </section>

  <section class="card card--brand" aria-label="Business card, brand side">
    <div class="wordmark">
      <span class="wordmark__square"></span>
      <span>Ridgefell<br>Construction</span>
    </div>
  </section>
</main>
</body>
</html>
```